Current state of Man's Soul Christian view

I would like an improvement of my design or a reimagining of my design to help people visualize what happens to the soul after we die. The second picture "screenshot 2023" is not my design but gives another idea.

For further information, there are 4 "time" frames that could be sectioned off. Eden is one time. Then adam rebellion and pre messiah earth (with hades/ Sheol). The third time frame is Jesus death, resurrection with the current state of earth. The 4th time frame is the "heavenly realm" which is across all 3 times and is unchanged.

For color ideas, please see my website www.lanternfieldnotes.org which has my color theme. But the death of Jesus I would like in some type of red as well as the death of believers.

My goal is something simple, engaging, and easy to understand. If you have any questions please lmk.
Thank you for considering my project.

```html
<!DOCTYPE html>
<html lang="en">
<head>
<meta charset="utf-8">
<title>Current State of Man's Soul</title>
<link rel="stylesheet" href="https://fonts.googleapis.com/css2?family=Bebas+Neue&family=Inter:wght@500;600;700&display=swap">
<style>
  :root{
    --page:#c9dfe6;
    --navy:#063a59;
    --navy-deep:#052e47;
    --red:#ec1c24;
    --red-bright:#ff3a40;
    --maroon:#3d0a1e;
    --gold:#f2b127;
    --panel:rgba(68,68,68,.86);
    --panel-line:rgba(255,255,255,.75);
    --white:#ffffff;
    --ink:#111111;
    --fallen-earth:#4a3f33;
    --current-earth:#2e5f8e;
    --torment:#c0301c;
    --paradise:#d8a650;
    --spirit:#2f6d96;
  }
  *{box-sizing:border-box;margin:0;padding:0}
  html,body{width:1200px;height:867px;overflow:hidden;background:var(--page)}
  body{font-family:"Inter",Arial,sans-serif;position:relative}
  .canvas{position:absolute;left:0;top:0;width:1200px;height:867px}
  .backdrop{position:absolute;left:32px;top:33px;width:1132px;height:800px;
    background:linear-gradient(180deg,#bcd2dc 0%,#d9e3e6 22%,#9fb4bb 42%,#4f7a86 55%,#7b8f92 68%,#bfb6a6 82%,#a49b8e 100%)}

  .title-bar{position:absolute;left:51px;top:49px;width:839px;height:77px;background:var(--navy);border-radius:8px}
  .title{position:absolute;left:23px;top:8px;font-family:"Bebas Neue",Impact,sans-serif;font-size:62px;line-height:66px;color:var(--white);letter-spacing:.5px;white-space:nowrap}
  .title-divider{position:absolute;left:635px;top:0;width:1px;height:77px;background:rgba(255,255,255,.6)}
  .brand{position:absolute;left:660px;top:24px;display:flex;align-items:center;gap:9px;color:var(--white);font-size:20px;font-weight:500}
  .brand-dot{width:14px;height:14px;border-radius:50%;background:var(--white)}

  .heaven{position:absolute;left:51px;top:143px;width:1084px;height:88px;border:1.5px solid #3b5563;border-radius:8px;
    background:linear-gradient(180deg,rgba(190,205,214,.75),rgba(150,175,190,.6))}
  .throne{position:absolute;left:440px;top:50px;width:200px;height:36px;border-radius:100px 100px 0 0;background:#b49a7e;opacity:.6}
  .heaven-title{position:absolute;left:0;right:0;top:12px;text-align:center;font-size:32px;font-weight:700;color:#2a2a2a;letter-spacing:-.5px}
  .badge{position:absolute;left:1007px;top:156px;width:113px;height:58px;background:var(--navy);border-radius:8px;color:var(--white);
    font-size:19px;font-weight:700;line-height:21px;text-align:center;padding-top:8px}
  .badge::after{content:"";position:absolute;left:50px;bottom:-8px;border:8px solid transparent;border-bottom:0;border-top-color:var(--navy)}

  .panel{position:absolute;background:var(--panel);border:1.5px solid var(--panel-line);border-radius:10px}
  .panel-past{left:113px;top:250px;width:449px;height:548px}
  .panel-now{left:740px;top:250px;width:391px;height:550px}

  .globe{position:absolute;border-radius:50%}
  .globe-fallen{left:255px;top:273px;width:198px;height:198px;background:var(--fallen-earth)}
  .globe-current{left:840px;top:313px;width:166px;height:166px;background:var(--current-earth)}

  .hades{position:absolute;width:164px;height:164px;border-radius:50%;overflow:hidden;display:flex}
  .hades-past{left:271px;top:595px}
  .hades-now{left:840px;top:594px}
  .torment{flex:1;background:var(--torment);border-right:2px solid var(--white)}
  .paradise{flex:1;background:var(--paradise)}
  .hades-label{position:absolute;font-size:14px;font-weight:600;color:var(--white)}
  .hades-label.on-light{color:#1a1a1a}

  .label-box{position:absolute;background:var(--white);border:1.5px solid #333;border-radius:5px;color:var(--ink);
    font-size:18px;font-weight:700;text-align:center;line-height:27px;white-space:nowrap}

  .adam{position:absolute;left:114px;top:250px;width:32px;height:300px;display:flex;align-items:center;justify-content:center}
  .adam span{transform:rotate(-90deg);white-space:nowrap;color:var(--white);font-size:22px;font-weight:600}
  .death-tab{position:absolute;left:160px;top:525px;width:91px;height:26px;background:var(--red);color:var(--white);
    font-size:21px;font-weight:700;line-height:28px;text-align:center;border-radius:3px 3px 0 0}
  .eden{position:absolute;left:42px;top:381px;width:56px;height:101px;border-radius:50%;background:var(--navy-deep)}
  .eden-text{position:absolute;left:-6px;top:38px;width:60px;transform:rotate(-90deg);color:var(--white);font-size:25px;font-weight:600;text-align:center;line-height:26px}
  .eden-arrow{position:absolute;left:36px;top:42px}

  .txt{position:absolute;color:var(--white);font-weight:600;white-space:nowrap}
  .gate{font-size:16px;line-height:16px}
  .jesus-death{left:481px;top:643px;font-size:22px;font-weight:700;line-height:24px;color:var(--red-bright)}
  .band-text{left:850px;top:550px;font-size:15px;font-weight:700}
  .believers{left:1003px;top:330px;font-size:20px;font-weight:700;line-height:24px;text-align:right}
  .resurrection{position:absolute;left:587px;top:342px;width:125px;height:51px;background:var(--white);border:2px solid #222;border-radius:6px;
    color:var(--navy);font-size:17px;font-weight:700;text-align:center;line-height:20px;padding-top:4px}
  .spirit{position:absolute;left:876px;top:250px;width:95px;height:56px;border-radius:4px;border:1px solid #9cc;
    background:var(--spirit);color:var(--white);font-size:13px;font-weight:600;line-height:14px;text-align:center;padding-top:7px}
  .overlay{position:absolute;left:0;top:0}
</style>
</head>
<body>
<div class="canvas">
  <div class="backdrop" role="img" aria-label="Photograph of a bright sky over the sea and a sandy beach"></div>

  <header class="title-bar">
    <h1 class="title">Current State of Man's Soul</h1>
    <div class="title-divider"></div>
    <div class="brand"><span class="brand-dot"></span>Lanternfield</div>
  </header>

  <section class="heaven">
    <div class="throne" role="img" aria-label="Heavenly throne illustration"></div>
    <h2 class="heaven-title">3rd Heaven - God’s Heavenly Throne</h2>
  </section>
  <div class="badge">Hidden in Messiah</div>

  <div class="panel panel-past"></div>
  <div class="panel panel-now"></div>

  <svg class="overlay" width="1200" height="867" viewBox="0 0 1200 867" aria-hidden="true">
    <defs>
      <g id="chev"><path d="M-8 -7 L0 0 L8 -7 M-8 1 L0 8 L8 1" fill="none" stroke="var(--gold)" stroke-width="3.5" stroke-linecap="round" stroke-linejoin="round"/></g>
    </defs>
    <g stroke="rgba(255,255,255,.85)" stroke-width="1.3" fill="none">
      <line x1="300" y1="516" x2="300" y2="612"/>
      <line x1="353" y1="516" x2="353" y2="596"/>
      <line x1="388" y1="516" x2="388" y2="600"/>
      <line x1="415" y1="516" x2="415" y2="622"/>
      <path d="M484 250 V632 Q484 645 470 645 H432"/>
      <line x1="432" y1="696" x2="562" y2="696"/>
      <line x1="856" y1="516" x2="856" y2="612"/>
      <line x1="909" y1="516" x2="909" y2="596"/>
      <line x1="945" y1="516" x2="945" y2="596"/>
      <line x1="972" y1="516" x2="972" y2="612"/>
      <line x1="917" y1="232" x2="917" y2="250"/>
      <line x1="929" y1="232" x2="929" y2="250"/>
    </g>
    <path d="M114 250 H146 V549 H1111 V259 H1130 V566 H114 Z" fill="var(--red)"/>
    <path d="M423 722 H640 Q650 722 650 712 V270" fill="none" stroke="var(--maroon)" stroke-width="8"/>
    <path d="M650 252 L637 290 L650 282 L663 290 Z" fill="var(--maroon)"/>
    <path d="M1004 393 H1112 Q1120 393 1120 385 V255" fill="none" stroke="var(--maroon)" stroke-width="7"/>
    <path d="M1120 237 L1108 262 L1120 256 L1132 262 Z" fill="var(--maroon)"/>
    <use href="#chev" x="326" y="584"/>
    <use href="#chev" x="402" y="584"/>
    <use href="#chev" x="882" y="533"/>
    <use href="#chev" x="959" y="533"/>
    <use href="#chev" x="882" y="585"/>
    <use href="#chev" x="959" y="585"/>
    <use href="#chev" x="923" y="241"/>
    <path d="M468 662 L460 670 L468 678 M476 662 L468 670 L476 678" fill="none" stroke="var(--red-bright)" stroke-width="4" stroke-linecap="round" stroke-linejoin="round"/>
    <g stroke="var(--red-bright)" stroke-width="4" stroke-linecap="round">
      <line x1="525" y1="575" x2="525" y2="625"/>
      <line x1="509" y1="587" x2="541" y2="587"/>
    </g>
  </svg>

  <div class="adam"><span>Adam Rebellion</span></div>
  <div class="death-tab">DEATH</div>
  <div class="eden">
    <div class="eden-text">Eden</div>
    <svg class="eden-arrow" width="16" height="18" viewBox="0 0 16 18" aria-hidden="true">
      <path d="M2 2 L8 9 L2 16 M8 2 L14 9 L8 16" fill="none" stroke="var(--gold)" stroke-width="3" stroke-linecap="round" stroke-linejoin="round"/>
    </svg>
  </div>

  <div class="globe globe-fallen" role="img" aria-label="Illustration of a darkened, burning fallen earth"></div>
  <div class="label-box" style="left:240px;top:487px;width:229px;height:30px">Pre-Messiah Fallen Earth</div>

  <div class="txt gate" style="left:213px;top:577px">Wide Gate</div>
  <div class="txt gate" style="left:424px;top:572px">Narrow<br>Gate</div>

  <div class="hades hades-past" role="img" aria-label="Illustration of Hades split into a fiery place of torment and a golden paradise gate">
    <div class="torment"></div><div class="paradise"></div>
  </div>
  <div class="hades-label" style="left:294px;top:620px">Torment</div>
  <div class="hades-label on-light" style="left:360px;top:620px">Paradise</div>
  <div class="txt" style="left:306px;top:763px;font-size:16px">Hades/Sheol</div>

  <div class="txt jesus-death">JESUS<br>DEATH</div>
  <div class="resurrection">Jesus Resurrection</div>

  <div class="spirit">Holy<br>Spirit<br>Descends</div>
  <div class="globe globe-current" role="img" aria-label="Illustration of the earth seen from space"></div>
  <div class="txt believers">Believers<br>in Jesus</div>
  <div class="label-box" style="left:830px;top:487px;width:187px;height:30px">Current Fallen Earth</div>
  <div class="txt band-text">Non-Believers Death</div>

  <div class="txt gate" style="left:763px;top:578px">Wide Gate</div>
  <div class="txt gate" style="left:987px;top:578px">Narrow Gate</div>

  <div class="hades hades-now" role="img" aria-label="Illustration of Hades split into a fiery place of torment and a golden paradise gate">
    <div class="torment"></div><div class="paradise"></div>
  </div>
  <div class="hades-label" style="left:862px;top:620px">Torment</div>
  <div class="hades-label on-light" style="left:928px;top:620px">Paradise</div>
  <div class="txt" style="left:876px;top:763px;font-size:16px">Hades/Sheol</div>
</div>
</body>
</html>
```